The most modern business card ever !!!

Our company call “Vendalo”. Vendalo is a technology company specialized in cruises solutions. Out main product is a platform to reserve cruises. This is a revolutionary platform that make easier to travel agencies and final users to reserve cruises across dozen companies like tibba, wernu, hpv, dgb, etc..We are a “start up”, with a young team of developers and we want to transmit it.. For it, we want something different, a modern business card that represent cruises and technology.. When someone receive this card, this person should say: wowww this is different… this is modern… this is a cruise related company..
- diferent, modern
- traditions business card

```html
<!DOCTYPE html>
<html lang="en">
<head>
<meta charset="utf-8">
<title>Vendalo Business Card</title>
<link href="https://fonts.googleapis.com/css2?family=Roboto:wght@400;500&family=Work+Sans:wght@400&display=swap" rel="stylesheet">
<style>
  :root {
    --stage: #8e8e8e;
    --ink: #151515;
    --paper: #ffffff;
    --accent: #29a8e0;
    --text: #1c1c1c;
  }
  * { box-sizing: border-box; margin: 0; padding: 0; }
  html, body { width: 1200px; height: 930px; overflow: hidden; }
  body { background: var(--stage); position: relative; font-family: "Work Sans", sans-serif; }

  .card {
    position: absolute;
    width: 620px;
    height: 354px;
    border-radius: 22px;
    overflow: hidden;
    box-shadow: 0 6px 14px rgba(0,0,0,0.25);
  }

  .card-front { left: 140px; top: 70px; background: var(--ink); display: flex; align-items: center; justify-content: center; }
  .card-front .brand { font-family: "Roboto", sans-serif; font-weight: 500; font-size: 66px; color: var(--paper); letter-spacing: 2px; }

  .card-back { left: 440px; top: 500px; background: var(--paper); }
  .card-back .wave { position: absolute; inset: 0; width: 620px; height: 354px; }
  .card-back .brand {
    position: absolute; right: 52px; top: 24px;
    font-family: "Roboto", sans-serif; font-weight: 500; font-size: 46px;
    color: var(--paper); letter-spacing: 1.5px;
  }

  .person { position: absolute; left: 150px; top: 206px; }
  .person .name { font-family: "Roboto", sans-serif; font-weight: 500; font-size: 23px; color: var(--accent); letter-spacing: 0.5px; }
  .person .role { font-size: 14px; color: var(--text); margin-top: 1px; }

  .divider { position: absolute; left: 150px; top: 268px; width: 412px; height: 1px; background: var(--accent); }

  .contacts { position: absolute; left: 150px; top: 280px; list-style: none; }
  .contacts li { display: flex; align-items: center; gap: 8px; font-size: 13px; color: var(--text); height: 21px; letter-spacing: 0.4px; }
  .contacts svg { width: 10px; height: 10px; flex: none; }

  .address { position: absolute; right: 58px; top: 282px; text-align: right; font-size: 13px; line-height: 20px; color: var(--text); letter-spacing: 0.4px; }
</style>
</head>
<body>

  <section class="card card-front" aria-label="Card front">
    <span class="brand">Vendalo</span>
  </section>

  <section class="card card-back" aria-label="Card back">
    <svg class="wave" viewBox="0 0 620 354" aria-hidden="true">
      <path fill="#151515" d="M0,0 H620 V84 C560,144 430,172 300,180 C190,187 70,218 0,304 Z"/>
      <path fill="#29a8e0" d="M0,0 H620 V78 C545,142 410,174 280,184 C150,194 55,225 0,276 Z"/>
      <path fill="none" stroke="#ffffff" stroke-width="4" d="M620,81 C552,143 420,173 290,182 C170,190 62,221 0,290"/>
      <path fill="#151515" d="M0,0 H620 V62 C540,128 400,158 270,166 C140,174 50,203 0,248 Z"/>
      <path fill="none" stroke="#ffffff" stroke-width="4" d="M620,62 C540,128 400,158 270,166 C140,174 50,203 0,248"/>
    </svg>

    <span class="brand">Vendalo</span>

    <div class="person">
      <p class="name">DANIEL REYES</p>
      <p class="role">Director</p>
    </div>

    <div class="divider"></div>

    <ul class="contacts">
      <li>
        <svg viewBox="0 0 10 10"><path fill="#29a8e0" d="M2,0.5 L3.6,2.6 L2.8,3.6 C3.4,5 4.8,6.5 6.3,7.2 L7.3,6.4 L9.5,8 L8.4,9.5 C4.5,9.3 0.7,5.5 0.5,1.6 Z"/></svg>
        <span>(514) 555-0182</span>
      </li>
      <li>
        <svg viewBox="0 0 10 10"><rect x="0.8" y="2" width="8.4" height="6" fill="none" stroke="#29a8e0" stroke-width="1"/><path d="M0.8,2 L5,5.4 L9.2,2" fill="none" stroke="#29a8e0" stroke-width="1"/></svg>
        <span>info@vendalo.com.br</span>
      </li>
      <li>
        <svg viewBox="0 0 10 10"><circle cx="5" cy="5" r="4.3" fill="none" stroke="#29a8e0" stroke-width="1"/><ellipse cx="5" cy="5" rx="1.8" ry="4.3" fill="none" stroke="#29a8e0" stroke-width="0.8"/><path d="M0.7,5 H9.3" stroke="#29a8e0" stroke-width="0.8"/></svg>
        <span>www.vendalo.com.br</span>
      </li>
    </ul>

    <p class="address">218b Harbour Lane,<br>Westport, NZ, 7825</p>
  </section>

</body>
</html>
```